BOLD & MINIMALIST DESIGN NEEDED

We want a very bold but minimalistic business card design that is impactful and utilizes both sides of the business card. Our current logo is included for your use.

We want bold fonts and good use of negative space. We don't want the logo to overpower the design.

Target Market(s)

Professionals who are building new commercial buildings.

Industry/Entity Type

Construction

Contact Information for Business Card

Name, Title, email, office phone, cell phone, website

Font styles to use
Serif
Sans Serif

Requirements
Must have
• Bold design!

```html
<!DOCTYPE html>
<html lang="en">
<head>
<meta charset="utf-8">
<title>Ridgeline Design + Build — Business Card</title>
<link rel="stylesheet" href="https://fonts.googleapis.com/css2?family=Montserrat:wght@400;500;800&display=swap">
<style>
  :root {
    --backdrop: #3b3b3b;
    --card-white: #ffffff;
    --card-black: #161616;
    --ink: #111111;
    --brand-green: #5a8f2e;
    --bright-green: #7cc142;
    --muted: #6f6f6f;
  }
  * { box-sizing: border-box; margin: 0; padding: 0; }
  html, body { width: 1200px; height: 791px; overflow: hidden; }
  body {
    background: var(--backdrop);
    font-family: "Montserrat", Arial, sans-serif;
    position: relative;
  }
  .card {
    position: absolute;
    top: 241px;
    width: 540px;
    height: 309px;
    border-bottom: 3px solid var(--brand-green);
    overflow: hidden;
  }
  .card--front { left: 40px; background: var(--card-white); }
  .card--back { left: 620px; background: var(--card-black); }

  .brand-name {
    position: absolute;
    left: 52px;
    top: 82px;
    display: flex;
    align-items: center;
    gap: 12px;
    color: var(--ink);
    font-weight: 800;
  }
  .brand-mark { width: 30px; height: 30px; background: var(--bright-green); flex: none; }
  .brand-text { display: flex; flex-direction: column; line-height: 1; }
  .brand-text .primary { font-size: 32px; letter-spacing: 0.5px; }
  .brand-text .secondary { font-size: 11px; letter-spacing: 5.4px; margin-top: 6px; }

  .divider {
    position: absolute;
    left: 318px;
    top: 96px;
    width: 1.5px;
    height: 86px;
    background: var(--brand-green);
  }

  .contact-list {
    position: absolute;
    left: 340px;
    top: 92px;
    list-style: none;
    font-size: 13px;
    color: var(--muted);
    line-height: 23px;
  }
  .contact-list li { display: flex; align-items: center; gap: 9px; }
  .contact-list svg { width: 11px; height: 11px; fill: var(--brand-green); flex: none; }

  .person {
    position: absolute;
    left: 52px;
    top: 216px;
  }
  .person .name {
    font-size: 22px;
    font-weight: 800;
    color: var(--brand-green);
    letter-spacing: 0.3px;
  }
  .person .title {
    font-size: 14px;
    color: var(--muted);
    margin-top: 2px;
    margin-left: 118px;
  }

  .back-pattern {
    position: absolute;
    inset: 0;
    background: radial-gradient(ellipse at 70% 40%, #2e2e2e 0%, #1c1c1c 55%, #0f0f0f 100%);
  }
  .back-brand {
    position: absolute;
    left: 50%;
    top: 50%;
    transform: translate(-50%, -50%);
    display: flex;
    align-items: center;
    gap: 10px;
    color: var(--card-white);
    font-weight: 800;
    font-size: 22px;
    letter-spacing: 0.5px;
  }
  .back-brand .brand-mark { width: 20px; height: 20px; }
</style>
</head>
<body>

<section class="card card--front" aria-label="Business card front">
  <div class="brand-name">
    <span class="brand-mark"></span>
    <span class="brand-text">
      <span class="primary">RIDGELINE</span>
      <span class="secondary">DESIGN + BUILD</span>
    </span>
  </div>

  <div class="divider"></div>

  <ul class="contact-list">
    <li>
      <svg viewBox="0 0 24 24" aria-hidden="true"><path d="M6.6 10.8a15.1 15.1 0 0 0 6.6 6.6l2.2-2.2a1 1 0 0 1 1-.25 11.4 11.4 0 0 0 3.6.6 1 1 0 0 1 1 1V20a1 1 0 0 1-1 1A17 17 0 0 1 3 4a1 1 0 0 1 1-1h3.5a1 1 0 0 1 1 1c0 1.25.2 2.45.6 3.6a1 1 0 0 1-.25 1z"/></svg>
      555-014-2200
    </li>
    <li>
      <svg viewBox="0 0 24 24" aria-hidden="true"><path d="M7 1h10a2 2 0 0 1 2 2v18a2 2 0 0 1-2 2H7a2 2 0 0 1-2-2V3a2 2 0 0 1 2-2zm0 3v14h10V4z"/></svg>
      555-014-2201
    </li>
    <li>
      <svg viewBox="0 0 24 24" aria-hidden="true"><path d="M2 5h20v14H2zm2 2v.5l8 5 8-5V7z"/></svg>
      m.trent@rdb-build.com
    </li>
    <li>
      <svg viewBox="0 0 24 24" aria-hidden="true"><circle cx="12" cy="12" r="10"/></svg>
      www.rdb-build.com
    </li>
  </ul>

  <div class="person">
    <p class="name">MARCUS TRENT</p>
    <p class="title">President</p>
  </div>
</section>

<section class="card card--back" aria-label="Business card back">
  <div class="back-pattern" role="img" aria-label="Repeating tonal pattern of the company emblem on a black ground"></div>
  <div class="back-brand">
    <span class="brand-mark"></span>
    <span>RIDGELINE</span>
  </div>
</section>

</body>
</html>
```